Meadowrun Acres Website Design

We have been redeveloping our website already and are quite happy with the content, but the design needs to be better:
https://tilvexa-hub.examplehost.net/

Pages, content, concept etc. Can all be taken from the redeveloped website.
The farmer can register and edit/view their profile, subscribe and these pages need to be designed better as well as contact, about, pricing, tos, privacy and a page with example portlets.

We need a website to appeal to farmers, investors and retiring farmers.

The design should be clean and a little country.

We don't want any repeat designs that some may submit to every project and has no respect for the project brief, so please don't submit them.

Target Market(s)

farmers, investors, retirees

Industry/Entity Type

Farming

Number of Pages Required

5+ page

Colors

Designer to choose colors to be used in the design.

Requirements
Must have
• Nice, clean modern design that is appealing
• Profile page laid out nicely

```html
<!DOCTYPE html>
<html lang="en">
<head>
<meta charset="utf-8">
<title>Meadowrun Acres</title>
<link href="https://fonts.googleapis.com/css2?family=Montserrat:wght@300;400;500;600;700&display=swap" rel="stylesheet">
<style>
:root{
  --green:#3fa535;
  --green-dark:#2f8a28;
  --footer-btn:#1f5a1b;
  --ink:#222;
  --text:#555;
  --muted:#888;
  --band:#f1f1f1;
  --white:#fff;
  --line:#e2e2e2;
}
*{box-sizing:border-box;margin:0;padding:0}
html,body{width:1200px;height:3255px;overflow:hidden}
body{font-family:'Montserrat',sans-serif;color:var(--text);background:var(--white);position:relative}
section,header,footer{position:absolute;left:0;width:1200px}
a{color:inherit;text-decoration:none}

/* header */
.site-header{top:0;height:120px;background:var(--white)}
.brand{position:absolute;left:100px;top:28px;display:flex;align-items:center;gap:14px}
.brand-dot{width:62px;height:62px;border-radius:50%;border:3px solid var(--green)}
.brand-name{font-weight:700;font-size:21px;color:var(--ink)}
.main-nav{position:absolute;left:423px;top:59px;display:flex;gap:29px;font-size:13px;color:#444;white-space:nowrap}
.login-btn{position:absolute;left:1015px;top:53px;width:88px;height:30px;background:var(--green);color:var(--white);font-size:17px;display:flex;align-items:center;justify-content:center}

/* hero */
.hero{top:120px;height:580px}
.hero-photo{position:absolute;inset:0;background:linear-gradient(180deg,#b9b6a2 0%,#8f8a6a 30%,#5e6a3a 55%,#4a5a2a 75%,#3a4a22 100%)}
.hero-title{position:absolute;top:172px;width:100%;text-align:center;color:var(--white);font-weight:600;font-size:96px;letter-spacing:1px}
.hero-lead{position:absolute;top:288px;left:200px;width:800px;text-align:center;color:var(--white);font-size:18px;line-height:28px;letter-spacing:.5px}
.hero-wave{position:absolute;left:0;bottom:0}
.hero-dots{position:absolute;top:522px;left:560px;display:flex;gap:4px}
.hero-dots span{width:16px;height:16px;border-radius:50%;background:var(--white)}
.hero-dots span.active{background:transparent;border:2px solid var(--white)}

/* welcome */
.welcome{top:700px;height:552px;text-align:center}
.section-title{font-weight:400;font-size:41px;color:var(--ink)}
.welcome .section-title{margin-top:44px}
.welcome-lead{width:760px;margin:22px auto 0;font-size:13px;line-height:24px;color:var(--muted)}
.welcome-rule{width:720px;height:1px;background:#eee;margin:30px auto 0}
.audiences{position:absolute;top:230px;left:92px;display:flex;gap:50px}
.audience{width:302px}
.audience-icon{width:150px;height:150px;margin:0 auto;border-radius:50%;background:var(--green);border:6px solid #e8f2e6;display:flex;align-items:center;justify-content:center}
.audience h3{margin-top:20px;font-weight:500;font-size:20px;color:var(--ink);letter-spacing:.5px}
.audience p{margin-top:12px;font-size:13px;line-height:21px;color:var(--text)}

/* own a farm */
.own-farm{top:1252px;height:478px;background:var(--band);text-align:center}
.own-farm .section-title{margin-top:58px}
.farm-cards{position:absolute;top:143px;left:100px;display:flex;gap:30px}
.farm-card{width:318px;height:260px;background:var(--white);border:1px solid var(--line);padding:4px}
.farm-card .photo{height:210px}
.farm-card p{margin-top:14px;font-size:14px;font-weight:700;color:var(--green)}

/* video */
.video{top:1730px;height:657px;text-align:center}
.video .section-title{margin-top:58px}
.video-frame{position:absolute;top:134px;left:100px;width:1000px;height:432px;border:1px solid #eee;padding:10px}
.video-still{width:100%;height:100%;background:linear-gradient(180deg,#6d7a3c 0%,#8a8f55 45%,#5a6040 100%);position:relative}
.play-btn{position:absolute;left:50%;top:50%;transform:translate(-50%,-50%)}

/* gallery */
.gallery{top:2387px;height:525px;background:var(--band);text-align:center}
.gallery .section-title{margin-top:58px}
.gallery-strip{position:absolute;top:143px;left:98px;display:flex}
.gallery-strip div{width:251px;height:206px}
.gallery-arrow{position:absolute;top:230px}
.view-more{position:absolute;top:413px;left:510px;width:180px;height:40px;border:2px solid #cde3c9;background:var(--white);color:var(--green);font-size:20px;display:flex;align-items:center;justify-content:center}

/* footer */
.site-footer{top:2912px;height:343px;background:var(--green);color:var(--white)}
.footer-brand{position:absolute;left:100px;top:68px;display:flex;align-items:center;gap:12px}
.footer-brand .brand-dot{width:56px;height:56px;border-color:var(--white)}
.footer-brand span{font-size:15px;font-weight:500}
.footer-about{position:absolute;left:100px;top:148px;width:290px;font-size:11px;line-height:19px}
.footer-col{position:absolute;top:44px}
.footer-col h4{font-size:18px;font-weight:600;letter-spacing:1px}
.footer-col ul{list-style:none;margin-top:16px;font-size:14px}
.footer-col li{height:32px}
.col-pages{left:440px}
.col-support{left:597px}
.col-news{left:773px}
.col-news p{margin-top:16px;font-size:13px}
.signup{display:flex;margin-top:16px}
.signup span{width:220px;height:40px;background:var(--white);color:#aaa;font-size:12px;letter-spacing:1px;display:flex;align-items:center;padding-left:16px}
.signup b{width:106px;height:40px;background:var(--footer-btn);font-size:13px;font-weight:500;display:flex;align-items:center;justify-content:center}
.social{display:flex;gap:12px;margin-top:14px}
.social span{width:38px;height:38px;border-radius:50%;background:var(--white)}
.footer-rule{position:absolute;left:100px;top:268px;width:1000px;height:1px;background:rgba(255,255,255,.45)}
.copyright{position:absolute;left:100px;top:294px;font-size:13px;letter-spacing:.5px}
</style>
</head>
<body>

<header class="site-header">
  <div class="brand"><span class="brand-dot"></span><span class="brand-name">Meadowrun Acres</span></div>
  <nav class="main-nav">
    <a>Home</a><a>Aspiring Farmers</a><a>Investors</a><a>Retiring Farmer</a><a>Blog</a><a>Pricing</a>
  </nav>
  <a class="login-btn">Log In</a>
</header>

<section class="hero">
  <div class="hero-photo" role="img" aria-label="Sunlit pasture with cattle grazing and a rider on horseback in front of rolling hills"></div>
  <h1 class="hero-title">Aspiring Farmers</h1>
  <p class="hero-lead">I really love to farm as farming is forever. I would love to farm anywhere there is an opportunity to live and work in a local farming community.</p>
  <svg class="hero-wave" width="1200" height="70" viewBox="0 0 1200 70">
    <path d="M0 20 C300 0 500 60 700 55 C900 50 1050 10 1200 15 L1200 70 L0 70Z" fill="var(--green)"/>
    <path d="M0 30 C300 10 500 70 700 65 C900 60 1050 22 1200 27 L1200 70 L0 70Z" fill="var(--white)"/>
  </svg>
  <div class="hero-dots"><span class="active"></span><span></span><span></span><span></span></div>
</section>

<section class="welcome">
  <h2 class="section-title">Welcome to Meadowrun Acres</h2>
  <p class="welcome-lead">We know how hard it is for a young family to find the capital required to own and operate their own farm - so we started Meadowrun Acres.</p>
  <div class="welcome-rule"></div>
  <div class="audiences">
    <div class="audience">
      <div class="audience-icon">
        <svg width="76" height="70" viewBox="0 0 76 70" fill="none" stroke="#fff" stroke-width="5"><path d="M6 30 L38 6 L70 30 V66 H6Z"/><rect x="20" y="38" width="36" height="28"/><path d="M20 38 L56 66 M56 38 L20 66"/><rect x="30" y="20" width="16" height="9"/></svg>
      </div>
      <h3>APPEAL TO FARMERS</h3>
      <p>We want to rejuvenate regional Australia by putting farming back up the top of the career list for anyone.</p>
    </div>
    <div class="audience">
      <div class="audience-icon">
        <svg width="88" height="62" viewBox="0 0 88 62">
          <rect x="0" y="12" width="14" height="28" fill="#fff" transform="rotate(-22 7 26)"/>
          <rect x="74" y="12" width="14" height="28" fill="#fff" transform="rotate(22 81 26)"/>
          <path d="M16 18 L32 12 L44 17 L56 12 L72 18 L70 36 L54 50 Q46 56 40 50 L24 40 L16 34Z" fill="#fff"/>
          <path d="M44 17 L34 26 Q38 30 46 24 L54 30" fill="none" stroke="var(--green)" stroke-width="2.5"/>
          <path d="M40 50 L32 42 M47 46 L38 37 M54 41 L45 32" fill="none" stroke="var(--green)" stroke-width="2.5"/>
        </svg>
      </div>
      <h3>INVESTORS</h3>
      <p>We want to rejuvenate regional Australia by putting farming back up the top of the career list for anyone.</p>
    </div>
    <div class="audience">
      <div class="audience-icon">
        <svg width="60" height="80" viewBox="0 0 60 80" fill="#fff"><circle cx="26" cy="12" r="10"/><path d="M10 30 Q26 20 42 30 L42 56 L10 56Z"/><rect x="12" y="56" width="10" height="22"/><rect x="30" y="56" width="10" height="22"/><rect x="48" y="36" width="4" height="42"/><path d="M42 36 Q50 28 54 36" stroke="#fff" stroke-width="4" fill="none"/></svg>
      </div>
      <h3>RETIRING FARMERS</h3>
      <p>We want to rejuvenate regional Australia by putting farming back up the top of the career list for anyone.</p>
    </div>
  </div>
</section>

<section class="own-farm">
  <h2 class="section-title">You Can Own A Farm</h2>
  <div class="farm-cards">
    <div class="farm-card">
      <div class="photo" role="img" aria-label="Young farming family on horseback with cattle in a green paddock" style="background:linear-gradient(180deg,#b8cfe0 0%,#9fb88a 45%,#6e8a4a 100%)"></div>
      <p>We connect a young farming family</p>
    </div>
    <div class="farm-card">
      <div class="photo" role="img" aria-label="Retiring farmer sitting with young children outside a timber shed" style="background:linear-gradient(180deg,#8a7f70 0%,#a07860 50%,#5e5a52 100%)"></div>
      <p>With a retiring farming family</p>
    </div>
    <div class="farm-card">
      <div class="photo" role="img" aria-label="Interior of an old wooden shearing shed" style="background:linear-gradient(180deg,#5e4a3a 0%,#8a6a4e 50%,#4a3a2e 100%)"></div>
      <p>And investors</p>
    </div>
  </div>
</section>

<section class="video">
  <h2 class="section-title">Our Video</h2>
  <div class="video-frame">
    <div class="video-still" role="img" aria-label="Video still of a farming family sitting together in the bush">
      <svg class="play-btn" width="86" height="86" viewBox="0 0 86 86"><circle cx="43" cy="43" r="39" fill="rgba(255,255,255,.15)" stroke="#fff" stroke-width="5"/><path d="M34 26 L62 43 L34 60Z" fill="#fff"/></svg>
    </div>
  </div>
</section>

<section class="gallery">
  <h2 class="section-title">Our Gallery</h2>
  <svg class="gallery-arrow" style="left:56px" width="20" height="34" viewBox="0 0 20 34"><path d="M17 2 L3 17 L17 32" stroke="#aaa" stroke-width="3" fill="none"/></svg>
  <div class="gallery-strip">
    <div role="img" aria-label="Wide blue sky over a flat paddock" style="background:linear-gradient(180deg,#3f7fb4 0%,#8ab4d4 70%,#6a5a3a 100%)"></div>
    <div role="img" aria-label="Workers tending crop rows beneath hills" style="background:linear-gradient(180deg,#6aa0d8 0%,#c9dcea 35%,#6d8a4a 60%,#4a6a2e 100%)"></div>
    <div role="img" aria-label="Open hay shed in a grassy field" style="background:linear-gradient(180deg,#c6ccd2 0%,#9aa0a0 45%,#6a7a4a 100%)"></div>
    <div role="img" aria-label="Red tractor working a ploughed field" style="background:linear-gradient(180deg,#2e6ec0 0%,#8ab8e0 50%,#b07a4a 75%,#8a5a3a 100%)"></div>
  </div>
  <svg class="gallery-arrow" style="left:1125px" width="20" height="34" viewBox="0 0 20 34"><path d="M3 2 L17 17 L3 32" stroke="#aaa" stroke-width="3" fill="none"/></svg>
  <a class="view-more">View More</a>
</section>

<footer class="site-footer">
  <div class="footer-brand"><span class="brand-dot"></span><span>Meadowrun Acres</span></div>
  <p class="footer-about">We can connect you with a passionate aspiring farming family who will love your farm just as much as you do. No registration required and your information will be kept private.</p>
  <div class="footer-col col-pages">
    <h4>PAGES</h4>
    <ul><li>Farmers</li><li>Investors</li><li>Retiring</li><li>About</li><li>Pricing</li></ul>
  </div>
  <div class="footer-col col-support">
    <h4>SUPPORT</h4>
    <ul><li>Contact</li><li>Terms of Service</li><li>Privacy</li><li>Donate</li></ul>
  </div>
  <div class="footer-col col-news">
    <h4>SIGN UP FOR NEWSLETTERS</h4>
    <p>Please sign up here for latest news</p>
    <div class="signup"><span>EMAIL ADDRESS</span><b>SUBSCRIBE</b></div>
    <div class="social"><span></span><span></span><span></span><span></span></div>
  </div>
  <div class="footer-rule"></div>
  <p class="copyright">© 2017 MEADOWRUN ACRES &nbsp; All right reserved &nbsp; Term of Use</p>
</footer>

</body>
</html>
```